Harbourline Physiotherapy business card design

We need a fresh, new business card design for our physiotherapy clinic Harbourline Physiotherapy

Will attach logo soon we had logo designed from our last project

Industry/Entity Type

Physical Therapy

Contact Information for Business Card

On front
Needs our logo, contact details:
58 Wexley Lane Fernvale Heights VIC 3981
Ph/f: 02 9481 2057
info@harbourlinephysio.example.com.au

Requirements
Must have
• On the back of the card needs to have area to write down follow up appointments
• On front
• Needs our logo
• The colours have to be the colours in our logo which are: sky blue, black and white
• Font to be same as our logo please
• We want the card to look simple, not too cluttered but to the point
Should not have
• We don't need any extra pictures other than our logo

```html
<!DOCTYPE html>
<html lang="en">
<head>
<meta charset="utf-8">
<title>Harbourline Physiotherapy – Business Card</title>
<link rel="stylesheet" href="https://fonts.googleapis.com/css2?family=Exo+2:wght@500;600;700&family=Open+Sans:wght@400;600;700&display=swap">
<style>
  :root {
    --sky: #3a9ad9;
    --sky-light: #6cc0ee;
    --violet: #5a5fc4;
    --ink: #2b2b2b;
    --grey: #5c5c5c;
    --band-dark: #262626;
    --band-mid: #4a4a4a;
    --paper: #ffffff;
    --page: #e9e7e3;
    --rule: #8a8a8a;
  }
  * { box-sizing: border-box; margin: 0; padding: 0; }
  html, body { width: 1200px; height: 692px; overflow: hidden; }
  body {
    background: var(--page);
    font-family: "Open Sans", Arial, sans-serif;
    color: var(--ink);
    position: relative;
  }
  .card {
    position: absolute;
    top: 191px;
    width: 540px;
    height: 309px;
    background: var(--paper);
    box-shadow: 0 6px 18px rgba(0,0,0,.18);
    overflow: hidden;
  }
  .card--front { left: 30px; }
  .card--back { left: 630px; }

  .brand { display: flex; align-items: center; gap: 10px; }
  .brand__dot {
    width: 22px; height: 22px;
    border-radius: 50%;
    background: var(--sky);
    flex: none;
  }
  .brand__name {
    font-family: "Exo 2", Arial, sans-serif;
    font-weight: 700;
    color: var(--sky);
    font-size: 24px;
    line-height: 1.05;
  }

  .card--front .brand { position: absolute; left: 34px; top: 62px; }
  .contact {
    position: absolute; left: 34px; top: 160px;
    font-size: 11.5px; line-height: 1.75; color: var(--grey);
    font-style: normal;
  }
  .contact__label { color: var(--sky); font-weight: 600; }
  .hours {
    position: absolute; right: 34px; top: 52px;
    font-size: 11.5px; line-height: 1.95; text-align: right; color: var(--grey);
  }
  .hours__day { color: var(--sky); font-weight: 700; }
  .services {
    position: absolute; left: 0; right: 0; bottom: 0; height: 62px;
    background: linear-gradient(90deg, var(--band-dark), var(--band-mid) 70%, var(--band-dark));
    color: #f2f2f2;
    display: flex; align-items: center; gap: 22px;
    padding: 0 30px;
  }
  .services__title { font-family: "Exo 2", Arial, sans-serif; font-weight: 600; font-size: 15px; white-space: nowrap; }
  .services__list { font-size: 10.5px; line-height: 1.8; }
  .services__sep { color: var(--sky-light); margin: 0 5px; }

  .card--back .brand { position: absolute; right: 28px; top: 36px; }
  .card--back .brand__name { font-size: 20px; text-align: right; }
  .tag {
    display: inline-block;
    background: linear-gradient(90deg, var(--sky-light), var(--violet));
    color: #fff;
    font-family: "Exo 2", Arial, sans-serif;
    font-weight: 600;
    text-transform: uppercase;
    padding: 3px 8px;
    letter-spacing: .3px;
  }
  .tag--large { font-size: 16px; }
  .tag--small { font-size: 12px; }
  .appointment { position: absolute; left: 30px; top: 100px; width: 480px; }
  .field-row {
    display: flex; align-items: flex-end; gap: 6px;
    font-size: 11px; font-weight: 600; text-transform: uppercase;
    margin-top: 14px;
  }
  .field-row__line { flex: 1; border-bottom: 1.5px dashed var(--rule); height: 12px; }
  .field-row__line--short { flex: 0 0 90px; }
  .days { display: flex; gap: 14px; margin-top: 16px; font-size: 11.5px; font-weight: 700; }
  .check { display: inline-flex; align-items: center; gap: 5px; }
  .box {
    display: inline-block; width: 13px; height: 13px;
    border: 1.5px solid var(--violet); border-radius: 2px;
  }
  .policy { margin-top: 18px; }
  .policy__text { margin-top: 7px; font-size: 11px; line-height: 1.55; color: var(--grey); max-width: 300px; }
</style>
</head>
<body>

<section class="card card--front" aria-label="Card front">
  <div class="brand">
    <span class="brand__dot"></span>
    <span class="brand__name">Harbourline<br>Physiotherapy</span>
  </div>

  <address class="contact">
    <div><span class="contact__label">Phone:</span> 02 9481 2057</div>
    <div>info@harbourlinephysio.example.com.au</div>
    <div>58 Wexley Lane, Fernvale Heights, VIC, 3981</div>
  </address>

  <div class="hours">
    <div><span class="hours__day">Mon:</span> 8am - 5.30pm</div>
    <div><span class="hours__day">Tues:</span> 10.30am - 8pm</div>
    <div><span class="hours__day">Wed:</span> 10am - 6pm</div>
    <div><span class="hours__day">Thur:</span> 10am - 6pm</div>
    <div><span class="hours__day">Fri:</span> 8am - 5.30pm</div>
  </div>

  <div class="services">
    <div class="services__title">Our Services:</div>
    <div class="services__list">
      <div>Hydrotherapy<span class="services__sep">&#9679;</span>Sports Injuries<span class="services__sep">&#9679;</span>Back &amp; Neck Pain</div>
      <div>Chronic Pain Management<span class="services__sep">&#9679;</span>Physiotherapy Treatment</div>
    </div>
  </div>
</section>

<section class="card card--back" aria-label="Card back">
  <div class="brand">
    <span class="brand__dot"></span>
    <span class="brand__name">Harbourline<br>Physiotherapy</span>
  </div>

  <div class="appointment">
    <span class="tag tag--large">Next Appointment</span>

    <div class="field-row">
      <span>Date:</span><span class="field-row__line"></span>
      <span>Time:</span><span class="field-row__line field-row__line--short"></span>
      <span class="check">AM <span class="box"></span></span>
      <span class="check">PM <span class="box"></span></span>
    </div>

    <div class="days">
      <span class="check">Mon <span class="box"></span></span>
      <span class="check">Tue <span class="box"></span></span>
      <span class="check">Wed <span class="box"></span></span>
      <span class="check">Thu <span class="box"></span></span>
      <span class="check">Fri <span class="box"></span></span>
      <span class="check">Sat <span class="box"></span></span>
      <span class="check">Sun <span class="box"></span></span>
    </div>

    <div class="field-row">
      <span>Name of Therapist:</span><span class="field-row__line"></span>
    </div>

    <div class="policy">
      <span class="tag tag--small">Cancellation Policy</span>
      <p class="policy__text">Minimum of 24hrs notice is required prior to appointment time or you will be charged $25 for the service.</p>
    </div>
  </div>
</section>

</body>
</html>
```